ambitious event and festival agency from austria needs fresh business card design

A new design is due for the new headquarters and the new challenges. We organize events for different target groups from 16 to 60 years. The design should therefore be straightforward and not confused, so we are open to new colors and the logo may also be changed. In general, however, the most interesting suggestions are the most interesting ones. after this order we are looking for more graphics for zirvanta facebook instagramm homepage etc A new design is due for the new headquarters and the new challenges. We organize events for different target groups from 16 to 60 years. The design should therefore be straightforward and not confused, so we are open to new colors and the logo may also be changed. In general, however, the most interesting suggestions are the most interesting ones. after this order we are looking for more graphics for zirvanta facebook instagramm homepage etc A new design is due for the new headquarters and the new challenges. We organize events for different target groups from 16 to 60 years. The design should therefore be straightforward and not confused, so we are open to new colors and the logo may also be changed. In general, however, the most interesting suggestions are the most interesting ones. after this order we are looking for more graphics for zirvanta facebook instagramm homepage etc
Updates

Reason: I am sorry for this decision but i need some more time. No new designs please, there are so many good ones and I will have made a decision in the next 3 days.

Target Market(s)

Industry/Entity Type

Business

Font styles to use
Serif
Sans Serif

Colors

Designer to choose colors to be used in the design.

Requirements
Must have
Nice to have
Should not have

```html
<!DOCTYPE html>
<html lang="en">
<head>
<meta charset="utf-8">
<title>zirvanta business card</title>
<link href="https://fonts.googleapis.com/css2?family=Oswald:wght@500&family=Work+Sans:wght@300;400;500&display=swap" rel="stylesheet">
<style>
  :root {
    --bg: #2a2a2c;
    --card-dark: #0d0d0e;
    --card-dark-edge: #262628;
    --paper: #ffffff;
    --crimson: #a41e34;
    --crimson-light: #b94a5b;
    --rule: #7a7a7a;
    --muted: #9a9a9a;
    --ink-soft: #f4e9eb;
  }
  * { box-sizing: border-box; margin: 0; padding: 0; }
  html, body { width: 1200px; height: 900px; overflow: hidden; background: var(--bg); }
  .canvas { position: relative; width: 1200px; height: 900px; }
  .card {
    position: absolute; left: 260px; width: 680px; height: 390px;
    border-radius: 26px; overflow: hidden;
    box-shadow: 0 18px 40px rgba(0,0,0,.45);
  }
  .card--back {
    top: 45px;
    background: linear-gradient(135deg, var(--card-dark-edge) 0%, var(--card-dark) 55%, #000 100%);
    display: flex; align-items: center; justify-content: center;
  }
  .card--front { top: 465px; background: var(--paper); }
  .wordmark {
    font-family: "Work Sans", sans-serif; font-weight: 500;
    color: var(--crimson); letter-spacing: 0.5px; line-height: 1;
    display: flex; align-items: center; gap: 10px;
  }
  .wordmark__dot { display: inline-block; background: var(--crimson); }
  .card--back .wordmark { font-size: 76px; }
  .card--back .wordmark__dot { width: 18px; height: 18px; }
  .card--front .wordmark { position: absolute; top: 52px; right: 42px; font-size: 54px; }
  .card--front .wordmark__dot { width: 13px; height: 13px; }
  .holder { position: absolute; left: 46px; top: 186px; }
  .holder__name {
    font-family: "Oswald", sans-serif; font-weight: 500; font-size: 28px;
    color: var(--crimson); text-transform: uppercase; letter-spacing: 0.2px;
    line-height: 1;
  }
  .holder__role {
    font-family: "Work Sans", sans-serif; font-weight: 300; font-size: 19px;
    color: var(--muted); margin-top: 2px;
  }
  .rule { position: absolute; left: 0; right: 0; top: 262px; height: 4px; background: var(--rule); }
  .band {
    position: absolute; left: 0; right: 0; top: 270px; bottom: 0;
    background: linear-gradient(90deg, var(--crimson-light) 0%, var(--crimson) 60%, var(--crimson) 100%);
    color: var(--paper); font-family: "Work Sans", sans-serif; font-weight: 300;
  }
  .contact { position: absolute; left: 46px; top: 18px; list-style: none; font-size: 20px; line-height: 27px; }
  .contact li { display: flex; align-items: center; gap: 12px; }
  .contact svg { width: 13px; height: 13px; flex: none; }
  .contact strong { font-weight: 500; }
  .address {
    position: absolute; right: 42px; top: 20px; text-align: right;
    font-size: 22px; line-height: 28px; font-style: normal; color: var(--ink-soft);
  }
</style>
</head>
<body>
<main class="canvas">
  <section class="card card--back" aria-label="Card back">
    <div class="wordmark"><span class="wordmark__dot"></span>zirvanta</div>
  </section>

  <section class="card card--front" aria-label="Card front">
    <div class="wordmark"><span class="wordmark__dot"></span>zirvanta</div>

    <div class="holder">
      <p class="holder__name">Markus Feldhofer</p>
      <p class="holder__role">Manager</p>
    </div>

    <div class="rule"></div>

    <div class="band">
      <ul class="contact">
        <li>
          <svg viewBox="0 0 12 12" fill="none" stroke="#fff" stroke-width="1.2"><rect x="3" y="0.8" width="6" height="10.4" rx="1"/><line x1="5" y1="9.4" x2="7" y2="9.4"/></svg>
          + 43 660 418 273 5
        </li>
        <li>
          <svg viewBox="0 0 12 12" fill="none" stroke="#fff" stroke-width="1.2"><rect x="0.8" y="2.5" width="10.4" height="7" rx="0.8"/><polyline points="1,3 6,7 11,3"/></svg>
          m.feldhofer@zirvanta.eu
        </li>
        <li>
          <svg viewBox="0 0 12 12" fill="none" stroke="#fff" stroke-width="1.1"><circle cx="6" cy="6" r="5.2"/><ellipse cx="6" cy="6" rx="2.3" ry="5.2"/><line x1="0.8" y1="6" x2="11.2" y2="6"/></svg>
          <span>www.<strong>zirvanta</strong>.eu</span>
        </li>
      </ul>
      <address class="address">zirvanta<br>Auberg 9<br>A4810 Gmundfeld</address>
    </div>
  </section>
</main>
</body>
</html>
```